Real Estate investment company needs billboard designs

This is our website: https://brightlanepropertygroup.com/
We are looking for some billboard concepts that uses our CEO in the design. I have attached some images and 1 billboard design that someone in our industry uses, but we don't want it exactly like his.

Industry/Entity Type

real estate

Colors

Designer to choose colors to be used in the design.

Requirements
Must have
• Company colors from websiute

```html
<!DOCTYPE html>
<html lang="en">
<head>
<meta charset="utf-8">
<title>Bright Lane Property Group – Billboard</title>
<link href="https://fonts.googleapis.com/css2?family=Barlow:wght@600;700&display=swap" rel="stylesheet">
<style>
  :root {
    --bg: #e6e6e6;
    --red: #ec1c24;
    --navy: #0c1c40;
    --white: #ffffff;
    --photo-top: #9fb6cf;
    --photo-bottom: #7f9cbc;
  }
  html, body {
    margin: 0;
    padding: 0;
    width: 1200px;
    height: 1200px;
    overflow: hidden;
    background: var(--bg);
  }
  .canvas {
    position: relative;
    width: 1200px;
    height: 1200px;
    font-family: "Barlow", Arial, sans-serif;
  }
  .billboard {
    position: absolute;
    left: 72px;
    top: 418px;
    width: 1056px;
    height: 332px;
    background: var(--navy);
    overflow: hidden;
  }
  .headline-band {
    position: absolute;
    left: 0;
    top: 0;
    width: 100%;
    height: 86px;
    background: var(--red);
    border-bottom: 6px solid var(--white);
  }
  .headline {
    position: absolute;
    top: 0;
    margin: 0;
    height: 86px;
    line-height: 88px;
    font-weight: 700;
    font-size: 82px;
    letter-spacing: 1px;
    color: var(--white);
    white-space: nowrap;
  }
  .headline--left { left: 36px; }
  .headline--right { left: 486px; }
  .headline .accent { color: var(--navy); }
  .ceo-photo {
    position: absolute;
    left: 0;
    top: 0;
    width: 1056px;
    height: 332px;
  }
  .offer {
    position: absolute;
    left: 558px;
    top: 112px;
    width: 480px;
    margin: 0;
    text-align: center;
    font-weight: 700;
    font-size: 46px;
    line-height: 64px;
    color: var(--white);
    white-space: nowrap;
  }
  .phone {
    position: absolute;
    left: 620px;
    top: 264px;
    width: 359px;
    height: 42px;
    box-sizing: border-box;
    background: var(--white);
    border-radius: 7px;
    display: flex;
    align-items: center;
    padding: 0 4px 0 20px;
  }
  .phone__number {
    flex: 1;
    font-weight: 700;
    font-size: 27px;
    letter-spacing: 3px;
    color: var(--navy);
  }
  .phone__call {
    background: var(--navy);
    color: var(--white);
    font-weight: 700;
    font-size: 25px;
    letter-spacing: 1px;
    border-radius: 5px;
    padding: 0 12px;
    line-height: 32px;
  }
  .brand {
    position: absolute;
    left: 44px;
    top: 252px;
    display: flex;
    align-items: center;
    gap: 8px;
  }
  .brand__square {
    width: 12px;
    height: 12px;
    background: var(--white);
  }
  .brand__name {
    font-weight: 700;
    font-size: 18px;
    line-height: 20px;
    color: var(--white);
    text-transform: uppercase;
  }
</style>
</head>
<body>
  <div class="canvas">
    <section class="billboard">
      <div class="headline-band"></div>
      <h1 class="headline headline--left">SELLING</h1>
      <h1 class="headline headline--right">YOUR <span class="accent">HOME?</span></h1>
      <svg class="ceo-photo" viewBox="0 0 1056 332" role="img" aria-label="Portrait of the company CEO, arms crossed, wearing a light blue denim shirt">
        <defs>
          <linearGradient id="photoTone" x1="0" y1="0" x2="0" y2="1">
            <stop offset="0" stop-color="var(--photo-top)"/>
            <stop offset="1" stop-color="var(--photo-bottom)"/>
          </linearGradient>
        </defs>
        <path d="M392 56 Q392 4 432 4 Q474 4 474 56 L474 100 Q556 110 566 150 L578 332 L308 332 L318 150 Q328 110 392 100 Z" fill="url(#photoTone)"/>
      </svg>
      <p class="offer">GET A CASH OFFER,<br>SAME DAY.</p>
      <div class="phone">
        <span class="phone__number">865-555-0142</span>
        <span class="phone__call">CALL</span>
      </div>
      <div class="brand">
        <span class="brand__square"></span>
        <span class="brand__name">Bright Lane<br>Property Group</span>
      </div>
    </section>
  </div>
</body>
</html>
```